Card design for orthopaedic surgeons working as The Brightwater Joint Centre

Business cards, letterhead

Colors

Designer to choose colors to be used in the design.

Requirements
Must have
• Late addition.
• Cards letterhead must have logos of
• Crestmoor Lindell College of Surgeons
• Varenwood Bone Health Association
Nice to have
• Back of card to have space for appointment time to be added by hand and some blank space for writing incidental other notes.

```html
<!DOCTYPE html>
<html lang="en">
<head>
<meta charset="utf-8">
<title>The Brightwater Joint Centre – Business Cards</title>
<link rel="stylesheet" href="https://fonts.googleapis.com/css2?family=Lato:wght@400;700&display=swap">
<style>
  :root {
    --bg: #e6e8ea;
    --card: #ffffff;
    --teal: #0a4a62;
    --teal-deep: #063a50;
    --blue: #2e9df0;
    --blue-soft: #cfe6f7;
    --ink: #3a3f44;
    --dots: #7a8088;
    --on-dark: #eaf4fb;
  }
  * { box-sizing: border-box; margin: 0; padding: 0; }
  html, body { width: 1200px; height: 960px; overflow: hidden; }
  body {
    background: var(--bg);
    font-family: "Lato", Arial, sans-serif;
    position: relative;
  }
  .card {
    position: absolute;
    width: 700px;
    height: 400px;
    background: var(--card);
    border-radius: 26px;
    overflow: hidden;
    box-shadow: 0 10px 28px rgba(0,0,0,0.18);
  }

  /* Appointment side */
  .card--appointment { left: 70px; top: 50px; }
  .brand-line {
    position: absolute;
    top: 42px; left: 0; width: 100%;
    text-align: center;
    color: var(--blue);
    font-size: 30px;
    letter-spacing: 0.3px;
  }
  .field {
    position: absolute;
    left: 50px;
    display: flex;
    align-items: flex-end;
    color: var(--blue);
    font-size: 20px;
    font-weight: 700;
  }
  .field .rule {
    flex: 1;
    border-bottom: 2px dotted var(--dots);
    margin-left: 8px;
    margin-bottom: 5px;
  }
  .field--name { top: 112px; width: 600px; }
  .field--date { top: 152px; width: 330px; }
  .field--time { top: 152px; left: 400px; width: 250px; }
  .ampm {
    position: absolute; top: 130px; right: 50px;
    color: var(--blue); font-size: 12px; font-weight: 700;
  }
  .days {
    position: absolute; top: 200px; left: 50px; width: 600px;
    display: flex; justify-content: space-between;
    color: var(--blue); font-size: 19px; font-weight: 700;
  }
  .day { display: flex; align-items: center; gap: 7px; }
  .box {
    width: 22px; height: 16px;
    border: 2px solid var(--teal-deep);
  }
  .field--note { top: 245px; width: 600px; }
  .blank-line {
    position: absolute; left: 50px; width: 600px;
    border-bottom: 2px dotted var(--dots);
  }
  .blank-line--1 { top: 305px; }
  .notice {
    position: absolute; top: 322px; left: 40px; width: 620px;
    text-align: center; color: var(--ink);
    font-size: 15px; line-height: 1.35;
  }

  /* Contact side */
  .card--contact { left: 430px; top: 500px; }
  .wave { position: absolute; inset: 0; }
  .contact-block { position: absolute; left: 44px; top: 52px; }
  .person-name {
    color: var(--blue); font-size: 30px; font-weight: 700;
    letter-spacing: 0.5px;
  }
  .person-role { color: var(--ink); font-size: 17px; font-weight: 700; margin-top: 2px; }
  .address { color: var(--ink); font-size: 17px; line-height: 1.3; margin-top: 14px; }
  .contact-list { list-style: none; margin-top: 12px; }
  .contact-list li {
    display: flex; align-items: center; gap: 10px;
    color: var(--ink); font-size: 16.5px; line-height: 1.45;
  }
  .contact-list svg { width: 16px; height: 16px; flex: none; }
  .member-badges {
    position: absolute; left: 44px; top: 322px;
    display: flex; gap: 12px;
  }
  .member-badge {
    width: 34px; height: 34px; border-radius: 50%;
    background: var(--blue-soft);
    border: 2px solid var(--blue);
  }
  .brand-on-dark {
    position: absolute; right: 22px; bottom: 56px;
    color: var(--on-dark); font-size: 21px; letter-spacing: 0.2px;
    white-space: nowrap;
  }
</style>
</head>
<body>

<section class="card card--appointment" aria-label="Appointment card">
  <div class="brand-line">The Brightwater Joint Centre</div>

  <div class="field field--name">Name :<span class="rule"></span></div>
  <div class="field field--date">Date :<span class="rule"></span></div>
  <div class="field field--time">Time :<span class="rule"></span></div>
  <div class="ampm">AM/PM</div>

  <div class="days">
    <span class="day">Sun <span class="box"></span></span>
    <span class="day">Mon <span class="box"></span></span>
    <span class="day">Tue <span class="box"></span></span>
    <span class="day">Wed <span class="box"></span></span>
    <span class="day">Thu <span class="box"></span></span>
    <span class="day">Fri <span class="box"></span></span>
    <span class="day">Sat <span class="box"></span></span>
  </div>

  <div class="field field--note">Note :<span class="rule"></span></div>
  <div class="blank-line blank-line--1"></div>

  <p class="notice">Please give me 24 hours notice if you are unable to keep your appointment or<br>a cancellation fee may be charged.</p>
</section>

<section class="card card--contact" aria-label="Contact card">
  <svg class="wave" viewBox="0 0 700 400" preserveAspectRatio="none" aria-hidden="true">
    <defs>
      <linearGradient id="tealFill" x1="0" y1="0" x2="1" y2="1">
        <stop offset="0" stop-color="#063a50"/>
        <stop offset="1" stop-color="#0b5670"/>
      </linearGradient>
    </defs>
    <path d="M700,60 C540,60 500,150 450,240 C400,330 330,385 200,400 L700,400 Z" fill="#063a50"/>
    <path d="M700,72 C552,74 514,158 466,246 C416,336 350,388 220,400 L700,400 Z" fill="url(#tealFill)"/>
    <path d="M650,62 C528,72 488,152 440,238 C390,326 320,380 190,396" fill="none" stroke="#2e9df0" stroke-width="5"/>
    <path d="M668,66 C542,78 502,158 454,244 C404,332 334,385 205,399" fill="none" stroke="#7cc6f7" stroke-width="2"/>
  </svg>

  <div class="contact-block">
    <div class="person-name">DANIEL HART</div>
    <div class="person-role">President</div>
    <div class="address">412 Larkspur Road<br>Fairhaven, Maine 04921</div>
    <ul class="contact-list">
      <li><svg viewBox="0 0 16 16"><path d="M3 1 L6 1 L7 5 L5 6 C6 8 8 10 10 11 L11 9 L15 10 L15 13 C15 14 14 15 13 15 C7 15 1 9 1 3 C1 2 2 1 3 1 Z" fill="#0a4a62"/></svg>555-214-0187</li>
      <li><svg viewBox="0 0 16 16"><rect x="4" y="1" width="8" height="14" rx="1.5" fill="none" stroke="#0a4a62" stroke-width="1.8"/><circle cx="8" cy="12.5" r="0.9" fill="#0a4a62"/></svg>555-318-0246</li>
      <li><svg viewBox="0 0 16 16"><rect x="4" y="1" width="8" height="4" fill="#0a4a62"/><rect x="1" y="6" width="14" height="6" rx="1" fill="#0a4a62"/><rect x="4" y="10" width="8" height="5" fill="#fff" stroke="#0a4a62" stroke-width="1.2"/></svg>555-427-0359</li>
      <li><svg viewBox="0 0 16 16"><rect x="1" y="3" width="14" height="10" rx="1" fill="#2e9df0"/><path d="M1 4 L8 9 L15 4" fill="none" stroke="#fff" stroke-width="1.4"/></svg>daniel@brightwaterjoint.com</li>
      <li><svg viewBox="0 0 16 16"><circle cx="8" cy="8" r="7" fill="#2e9df0"/><path d="M1 8 H15 M8 1 C5 4 5 12 8 15 M8 1 C11 4 11 12 8 15" fill="none" stroke="#fff" stroke-width="1"/></svg>www.brightwaterjoint.com</li>
    </ul>
  </div>

  <div class="member-badges">
    <span class="member-badge" role="img" aria-label="Crestmoor Lindell College of Surgeons membership badge"></span>
    <span class="member-badge" role="img" aria-label="Varenwood Bone Health Association membership badge"></span>
  </div>

  <div class="brand-on-dark">The Brightwater Joint Centre</div>
</section>

</body>
</html>
```